Venture Capital firm needs modern business cards

We are a Venture Capital firm within financial services/Asset management. The industry generally has basic business cards with black, blue and maybe green/yellow design elements.
Our firm has a four-colour swoosh logo. We are based in London and want to stand out, just a little bit!, from the crowd. Our company is called LORV Investments and the 'C' stands for collaboration thus using makerswarm is a natural portal for our business card design competition. Our logo came via makerswarm too!
We use 'Venture Partner in Asset Management' as our tagline and this is Trademark registered. We operate in a conservative industry and we should not overstep our mark. The logo is colorful as it is and therefore the rest of the design should not be too fanciful.
The objective is twofold: make our logo element stick and memorable with our audience, whilst representing a conservative yet young image.
Updates
The Business Card obviously needs a field for Name, Surname, Job Title, Adress fields: Street, City, Postcode, Country, telefone and cell number, website address, etc.
We have uploaded the ai file. We trust that these are OK. If not, please advise.
Reason: We have have been busy with a client engagement. We will set the project as Guaranteed in return for the troubles we cause. Apologies for the confusion.
Thank you all for these great and creative design suggestions. The team is very happy with a number of your ideas! We will be in touch tomorrow to give individual feedback before the project closes on Friday. We look forward to working with some of you to narrow down your creations. Thank you, LORV Investments team.
All,
Target Market(s)
Financial Services Professionals, Investors, Media, 35-70 years, mainly male, well educated
Industry/Entity Type
Conservative
Requirements
Must have
- We must make use of our logo and potential tagline 'Venture Partner in Asset Management' as we are establishing a new Brand and new company in the market.
We can use 'LORV', 'LORV Investments', and 'LORV Investments'+tagline 'Venture Partner in Asset Management' or simply the four-colour swoosh plus the name of the company as part of the text. (see files)
All design elements are available in black or grey-scale if required. (grey scale swoosh attached).
Due to regulation we must have the following wording on the card in small print 'LORV Investments is an Appointed Representative of Bramwell Holdings Partnership Limited, which is authorised by the Monetary Oversight Board'.
Nice to have
- We would consider designs that make use of different printing techniques such embossing/debossing, UV spot etc.
We attach our colour palette in the files section for your reference.
Should not have
- The font we use for our company name is 'EXO' so do not use a font style that clashes with the corporate fonts, please.
Do not use other design elements than the ones we provide in the file library as part of this project.

```html
<!DOCTYPE html>
<html lang="en">
<head>
<meta charset="utf-8">
<title>LORV Investments – Business Card Set</title>
<link rel="stylesheet" href="https://fonts.googleapis.com/css2?family=Arimo:wght@400&family=PT+Sans:wght@400&display=swap">
<style>
  :root {
    --board: #e6e7e8;
    --slate: #6b6c6f;
    --pink: #ee0f6a;
    --teal: #8acfd6;
    --paper: #ffffff;
    --ink-light: #ffffff;
    --ink-grey: #77787b;
    --mark-on-dark: #d9dadc;
    --mark-on-light: #c4c5c7;
    --mark-on-colour: rgba(255,255,255,0.78);
    --note-ink: #1a1a1a;
  }
  * { box-sizing: border-box; margin: 0; padding: 0; }
  html, body { width: 1200px; height: 800px; overflow: hidden; }
  body {
    position: relative;
    background: var(--board);
    font-family: "Arimo", Arial, sans-serif;
  }
  .card {
    position: absolute;
    border-radius: 1em;
    box-shadow: 3px 4px 5px rgba(0,0,0,0.28);
    overflow: hidden;
  }
  .card--slate { background: var(--slate); color: var(--ink-light); }
  .card--pink  { background: var(--pink);  color: var(--ink-light); }
  .card--teal  { background: var(--teal);  color: var(--ink-light); }
  .card--paper { background: var(--paper); color: var(--ink-grey); }

  /* brand name set where the die-cut mark sits */
  .brand-mark {
    position: absolute;
    left: 0; right: 0;
    top: 50%;
    transform: translateY(-50%);
    text-align: center;
    font-size: 2.6em;
    letter-spacing: 0.06em;
    line-height: 1;
  }
  .card--slate .brand-mark { color: var(--mark-on-dark); }
  .card--pink .brand-mark,
  .card--teal .brand-mark { color: var(--mark-on-colour); }
  .card--paper .brand-mark { color: var(--mark-on-light); }

  /* front side */
  .holder {
    position: absolute;
    top: 9%;
    right: 1.6em;
    text-align: right;
    line-height: 1.15;
  }
  .holder__name { font-size: 1.45em; display: block; }
  .holder__title { font-size: 1em; display: block; }

  /* back side */
  .contact-row {
    position: absolute;
    left: 1em; right: 1.8em;
    display: flex;
    justify-content: space-between;
    font-size: 1.1em;
    white-space: nowrap;
    transform: translateY(-50%);
    line-height: 1.2;
  }
  .contact-row--top { top: 6.5%; }
  .contact-row--phones { top: 79%; justify-content: flex-start; gap: 1.6em; left: 1.2em; }
  .contact-item { display: flex; align-items: center; gap: 0.55em; }
  .icon { width: 1.05em; height: 1.05em; flex: none; }
  .address {
    position: absolute;
    left: 1.2em;
    top: 86.5%;
    transform: translateY(-50%);
    font-size: 1.1em;
    line-height: 1.2;
    white-space: nowrap;
    display: flex; align-items: center; gap: 0.45em;
  }
  .fine-print {
    position: absolute;
    left: 2.5em; right: 2.2em;
    top: 90.3%;
    font-size: 0.6em;
    text-align: center;
    line-height: 1.2;
    padding-left: 3em;
  }

  /* placement on the board */
  .card--back-tilted {
    font-size: 12px;
    width: 425px; height: 240px;
    left: 104px; top: 108px;
    transform: rotate(-28.8deg);
    z-index: 3;
  }
  .card--front-white {
    font-size: 12px;
    width: 432px; height: 246px;
    left: 260px; top: 242px;
    z-index: 2;
  }
  .card--front-pink {
    font-size: 8.9px;
    width: 318px; height: 182px;
    left: 802px; top: 47px;
  }
  .card--back-small {
    font-size: 8.9px;
    width: 318px; height: 183px;
    left: 802px; top: 247px;
  }
  .card--front-teal {
    font-size: 10px;
    width: 356px; height: 203px;
    left: 94px; top: 545px;
  }
  .card--back-large {
    font-size: 10px;
    width: 355px; height: 202px;
    left: 475px; top: 542px;
  }

  .presentation-note {
    position: absolute;
    left: 807px; top: 480px;
    font-family: "PT Sans", Arial, sans-serif;
    font-size: 14px;
    color: var(--note-ink);
  }
</style>
</head>
<body>

<svg width="0" height="0" style="position:absolute" aria-hidden="true">
  <defs>
    <symbol id="i-mail" viewBox="0 0 16 16"><rect x="1.5" y="3.5" width="13" height="9" fill="none" stroke="currentColor" stroke-width="1.2"/><path d="M1.5 3.5 8 9l6.5-5.5" fill="none" stroke="currentColor" stroke-width="1.2"/></symbol>
    <symbol id="i-web" viewBox="0 0 16 16"><circle cx="8" cy="8" r="6.5" fill="none" stroke="currentColor" stroke-width="1.2"/><ellipse cx="8" cy="8" rx="2.8" ry="6.5" fill="none" stroke="currentColor" stroke-width="1.1"/><path d="M1.5 8h13M2.6 4.6h10.8M2.6 11.4h10.8" stroke="currentColor" stroke-width="1.1"/></symbol>
    <symbol id="i-phone" viewBox="0 0 16 16"><path d="M4 1.8 6 4.2 4.8 6.1c.9 2 2.5 3.6 4.6 4.6l1.8-1.2 2.5 2-1.1 2.3C7 13.5 2.4 8.9 2.1 2.9Z" fill="none" stroke="currentColor" stroke-width="1.2" stroke-linejoin="round"/></symbol>
    <symbol id="i-mobile" viewBox="0 0 16 16"><rect x="4.2" y="1.2" width="7.6" height="13.6" rx="1.2" fill="none" stroke="currentColor" stroke-width="1.2"/><path d="M4.2 11.8h7.6" stroke="currentColor" stroke-width="1.1"/></symbol>
    <symbol id="i-home" viewBox="0 0 16 16"><path d="M1.5 8 8 2l6.5 6M3.5 6.5V14h9V6.5M6.5 14v-4h3v4" fill="none" stroke="currentColor" stroke-width="1.2" stroke-linejoin="round"/></symbol>
  </defs>
</svg>

<!-- tilted back -->
<div class="card card--slate card--back-tilted">
  <div class="contact-row contact-row--top">
    <span class="contact-item"><svg class="icon"><use href="#i-mail"/></svg>daniel@lorvinvestments.com</span>
    <span class="contact-item"><svg class="icon"><use href="#i-web"/></svg>www.lorvinvestments.com</span>
  </div>
  <div class="brand-mark">LORV</div>
  <div class="contact-row contact-row--phones">
    <span class="contact-item"><svg class="icon"><use href="#i-phone"/></svg>+1 (800) 555-0142</span>
    <span class="contact-item"><svg class="icon"><use href="#i-mobile"/></svg>+1 (800) 555-0142</span>
  </div>
  <div class="address"><svg class="icon"><use href="#i-home"/></svg>12 Kestrel Road, 9 Alder Square, London, United Kingdom</div>
  <p class="fine-print">'LORV Investments is an Appointed Representative of Bramwell Holdings Partnership Limited, which is authorised by the Monetary Oversight Board'.</p>
</div>

<!-- white front -->
<div class="card card--paper card--front-white">
  <div class="holder"><span class="holder__name">Daniel Harrow</span><span class="holder__title">Chairman</span></div>
  <div class="brand-mark">LORV</div>
</div>

<!-- pink front -->
<div class="card card--pink card--front-pink">
  <div class="holder"><span class="holder__name">Daniel Harrow</span><span class="holder__title">Chairman</span></div>
  <div class="brand-mark">LORV</div>
</div>

<!-- small back -->
<div class="card card--slate card--back-small">
  <div class="contact-row contact-row--top">
    <span class="contact-item"><svg class="icon"><use href="#i-mail"/></svg>daniel@lorvinvestments.com</span>
    <span class="contact-item"><svg class="icon"><use href="#i-web"/></svg>www.lorvinvestments.com</span>
  </div>
  <div class="brand-mark">LORV</div>
  <div class="contact-row contact-row--phones">
    <span class="contact-item"><svg class="icon"><use href="#i-phone"/></svg>+1 (800) 555-0142</span>
    <span class="contact-item"><svg class="icon"><use href="#i-mobile"/></svg>+1 (800) 555-0142</span>
  </div>
  <div class="address"><svg class="icon"><use href="#i-home"/></svg>12 Kestrel Road, 9 Alder Square, London, United Kingdom</div>
  <p class="fine-print">'LORV Investments is an Appointed Representative of Bramwell Holdings Partnership Limited, which is authorised by the Monetary Oversight Board'.</p>
</div>

<p class="presentation-note">• Note : Three colour options,&nbsp; swoosh is die cut.</p>

<!-- teal front -->
<div class="card card--teal card--front-teal">
  <div class="holder"><span class="holder__name">Daniel Harrow</span><span class="holder__title">Chairman</span></div>
  <div class="brand-mark">LORV</div>
</div>

<!-- large back -->
<div class="card card--slate card--back-large">
  <div class="contact-row contact-row--top">
    <span class="contact-item"><svg class="icon"><use href="#i-mail"/></svg>daniel@lorvinvestments.com</span>
    <span class="contact-item"><svg class="icon"><use href="#i-web"/></svg>www.lorvinvestments.com</span>
  </div>
  <div class="brand-mark">LORV</div>
  <div class="contact-row contact-row--phones">
    <span class="contact-item"><svg class="icon"><use href="#i-phone"/></svg>+1 (800) 555-0142</span>
    <span class="contact-item"><svg class="icon"><use href="#i-mobile"/></svg>+1 (800) 555-0142</span>
  </div>
  <div class="address"><svg class="icon"><use href="#i-home"/></svg>12 Kestrel Road, 9 Alder Square, London, United Kingdom</div>
  <p class="fine-print">'LORV Investments is an Appointed Representative of Bramwell Holdings Partnership Limited, which is authorised by the Monetary Oversight Board'.</p>
</div>

</body>
</html>
```